Chocolate Bar Design

I need packaging design for a new line of chocolate bars.

The new design must fit in with the packaging design for our line of solid chocolate bars. The previous bars are packaged in clear boxes, the new line is in 3x3 kraft boxes so the new design must be visusally appealing, and portray what lies inside as they are not able to view the bar itself.

The new product line is for "Truffle Bars", basically a chocolate bar with a truffle filling. The first three flavors are Velmora Ember (Cinnamon and Cayenne, Sea Salt), Cafe Mocha, and Pumpkin Pie.

These are artisan bars, and should reflect in the packaging.

If you view our previous packaging, they are the same design but with a different color for each flavor, which would be ideal.

Industry/Entity Type

Cafe

Requirements
Must have
• Each design should include the front label that has the company name, size of the bar, and name of the bar at minimum. The reverse label must have company name, address, website, and ingredients, at minimum.

Nice to have
• Ideally, I would be able to edit ingredients, and bar names easily.

```html
<!DOCTYPE html>
<html lang="en">
<head>
<meta charset="utf-8">
<title>Corvin Hale Truffle Bar Labels</title>
<link rel="stylesheet" href="https://fonts.googleapis.com/css2?family=Gelasio:ital,wght@0,400;0,700;1,700&display=swap">
<style>
  :root {
    --canvas: #ffffff;
    --kraft-gold: #c3a262;
    --label-white: #ffffff;
    --ink: #141414;
    --title-gold: #c8a866;

    --mocha-outer: #9a6d4e;
    --mocha-core: #6a3e2c;
    --ember-outer: #b45b33;
    --ember-core: #88250f;
    --pumpkin-outer: #ef6b2d;
    --pumpkin-core: #e83f2e;
  }
  * { margin: 0; padding: 0; box-sizing: border-box; }
  html, body {
    width: 1200px;
    height: 427px;
    overflow: hidden;
    background: var(--canvas);
  }
  .sheet {
    position: relative;
    width: 1200px;
    height: 427px;
  }
  .label {
    position: absolute;
    top: 27px;
    width: 370px;
    height: 370px;
    background: var(--kraft-gold);
  }
  .label--mocha { left: 27px; }
  .label--ember { left: 415px; }
  .label--pumpkin { left: 803px; }

  .label__face {
    position: absolute;
    left: 33px;
    top: 31px;
    width: 305px;
    height: 310px;
    background: var(--label-white);
    border-radius: 20px;
    overflow: hidden;
  }
  .brand {
    position: absolute;
    top: 30px;
    left: 0;
    width: 100%;
    text-align: center;
    font-family: "Gelasio", Georgia, serif;
    font-weight: 400;
    color: var(--ink);
    font-size: 30px;
    line-height: 1.1;
    letter-spacing: 0.5px;
  }
  .flavour-band {
    position: absolute;
    top: 129px;
    left: 0;
    width: 100%;
    height: 135px;
    background: var(--band-outer);
  }
  .flavour-band__title {
    position: absolute;
    top: 10px;
    left: 0;
    width: 100%;
    height: 53px;
    background: var(--band-core);
    color: var(--title-gold);
    font-family: "Gelasio", Georgia, serif;
    font-weight: 700;
    font-size: 30px;
    line-height: 53px;
    text-align: center;
    white-space: nowrap;
  }
  .flavour-band__tagline {
    position: absolute;
    top: 72px;
    left: 0;
    width: 100%;
    text-align: center;
    font-family: "Gelasio", Georgia, serif;
    font-style: italic;
    font-weight: 700;
    font-size: 16.5px;
    line-height: 23px;
    color: var(--ink);
  }
  .net-weight {
    position: absolute;
    top: 272px;
    left: 0;
    width: 100%;
    text-align: center;
    font-family: "Gelasio", Georgia, serif;
    font-size: 12px;
    color: var(--ink);
    letter-spacing: 0.2px;
  }
  .label--mocha { --band-outer: var(--mocha-outer); --band-core: var(--mocha-core); }
  .label--ember { --band-outer: var(--ember-outer); --band-core: var(--ember-core); }
  .label--pumpkin { --band-outer: var(--pumpkin-outer); --band-core: var(--pumpkin-core); }
</style>
</head>
<body>
<main class="sheet">
  <section class="label label--mocha">
    <div class="label__face">
      <p class="brand">Corvin Hale<br>Chocolates</p>
      <div class="flavour-band">
        <h2 class="flavour-band__title">Cafe Mocha</h2>
        <p class="flavour-band__tagline">Exclusively Hand-Crafted<br>Chocolate Bar with Truffle filling</p>
      </div>
      <p class="net-weight">NET WT. 2,5 OZ / 70 G</p>
    </div>
  </section>

  <section class="label label--ember">
    <div class="label__face">
      <p class="brand">Corvin Hale<br>Chocolates</p>
      <div class="flavour-band">
        <h2 class="flavour-band__title">Velmora Ember</h2>
        <p class="flavour-band__tagline">Exclusively Hand-Crafted<br>Chocolate Bar with Truffle filling</p>
      </div>
      <p class="net-weight">NET WT. 2,5 OZ / 70 G</p>
    </div>
  </section>

  <section class="label label--pumpkin">
    <div class="label__face">
      <p class="brand">Corvin Hale<br>Chocolates</p>
      <div class="flavour-band">
        <h2 class="flavour-band__title">Pumpkin Pie</h2>
        <p class="flavour-band__tagline">Exclusively Hand-Crafted<br>Chocolate Bar with Truffle filling</p>
      </div>
      <p class="net-weight">NET WT. 2,5 OZ / 70 G</p>
    </div>
  </section>
</main>
</body>
</html>
```